Executive Business Card for Healthcare Company [Need Today]

I need a business card design for a healthcare company. The only branding the company has thus far is a logo. The cards will be utilized by company executives. The design I envision will be vibrant and appealing but with a corporate feel. They shouldn't be too casual or playful. I would like to complete this project TODAY if possible.

Target Market(s)

Healthcare vendors, other executives in healthcare and pharmaceuticals

Industry/Entity Type

Pharmaceutical

Contact Information for Business Card

See attachment

Font styles to use
Serif
Sans Serif

Colors

Designer to choose colors to be used in the design.

```html
<!DOCTYPE html>
<html lang="en">
<head>
<meta charset="utf-8">
<title>Tessaly Therapeutics – Business Card</title>
<link rel="stylesheet" href="https://fonts.googleapis.com/css2?family=Fira+Sans:wght@400;500&display=swap">
<style>
  :root {
    --teal: #38bfc7;
    --white: #ffffff;
    --backdrop: #e6e6e4;
    --card-edge: #d4d4d2;
  }
  * { box-sizing: border-box; margin: 0; padding: 0; }
  html, body {
    width: 1200px; height: 1000px; overflow: hidden;
    background: var(--backdrop);
    font-family: "Fira Sans", sans-serif;
  }
  .canvas { position: relative; width: 1200px; height: 1000px; }

  .card { position: absolute; width: 596px; height: 339px; }
  .card--front {
    left: 169px; top: 112px;
    background: var(--white);
    border: 1px solid var(--card-edge);
  }
  .card--back {
    left: 390px; top: 558px; width: 599px; height: 340px;
    background: var(--teal); color: var(--white);
  }

  /* wordmark: plain circle + company name */
  .wordmark { position: absolute; display: flex; align-items: center; gap: 10px; }
  .wordmark__circle { border-radius: 50%; border: 2px solid currentColor; flex: none; }
  .wordmark__name { font-weight: 400; line-height: 1; }
  .wordmark__main { display: block; font-size: 28px; letter-spacing: 1px; }
  .wordmark__sub { display: block; font-size: 14px; margin-top: 3px; text-align: right; }

  .card--front .wordmark { left: 333px; top: 134px; color: var(--teal); }
  .card--front .wordmark__circle { width: 56px; height: 56px; }

  .card--back .wordmark { left: 343px; top: 56px; color: var(--white); }
  .card--back .wordmark__circle { width: 68px; height: 68px; }

  .holder { position: absolute; left: 39px; top: 66px; }
  .holder__name { font-size: 30px; font-weight: 500; letter-spacing: 2.5px; line-height: 1.1; }
  .holder__title { font-size: 17px; font-weight: 400; margin-top: 8px; }

  .divider {
    position: absolute; left: 37px; top: 162px; width: 521px; height: 1px;
    background: var(--white);
  }

  .contacts { position: absolute; left: 38px; top: 180px; list-style: none; }
  .contacts__item {
    display: flex; align-items: center; gap: 16px;
    font-size: 20px; letter-spacing: 1px; height: 27px;
  }
  .contacts__icon { width: 18px; height: 16px; fill: var(--white); flex: none; }

  .company {
    position: absolute; left: 0; right: 0; top: 281px;
    text-align: center; font-size: 15px; line-height: 19px;
  }
</style>
</head>
<body>
<main class="canvas">

  <section class="card card--front" aria-label="Card front">
    <div class="wordmark">
      <span class="wordmark__circle"></span>
      <span class="wordmark__name">
        <span class="wordmark__main">tessaly</span>
        <span class="wordmark__sub">therapeutics</span>
      </span>
    </div>
  </section>

  <section class="card card--back" aria-label="Card back">
    <div class="holder">
      <h1 class="holder__name">Daniel Marsh</h1>
      <p class="holder__title">Senior Director of Marketing</p>
    </div>

    <div class="wordmark">
      <span class="wordmark__circle"></span>
      <span class="wordmark__name">
        <span class="wordmark__main">tessaly</span>
        <span class="wordmark__sub">therapeutics</span>
      </span>
    </div>

    <div class="divider"></div>

    <ul class="contacts">
      <li class="contacts__item">
        <svg class="contacts__icon" viewBox="0 0 18 16" aria-hidden="true">
          <path d="M1 5c0-2 3-3 8-3s8 1 8 3v1h-4V4.5H5V6H1z"/>
          <rect x="3" y="7" width="12" height="8" rx="1"/>
        </svg>
        555-014-2287
      </li>
      <li class="contacts__item">
        <svg class="contacts__icon" viewBox="0 0 18 16" aria-hidden="true">
          <path d="M4 1l3 3-2 2c1 2 3 4 5 5l2-2 3 3-2 3C7 14 3 10 2 4z"/>
        </svg>
        555-016-4410
      </li>
      <li class="contacts__item">
        <svg class="contacts__icon" viewBox="0 0 18 16" aria-hidden="true">
          <path d="M1 3h16v1l-8 5-8-5z"/>
          <path d="M1 6l8 5 8-5v7H1z"/>
        </svg>
        dmarsh@tessalyrx.com
      </li>
    </ul>

    <address class="company" style="font-style:normal">
      TESSALY THERAPEUTICS, LLC<br>
      118 N Orchard Avenue, Milford, GA 30000
    </address>
  </section>

</main>
</body>
</html>
```